Business card for my new company (Accounting firm)

I need a business card for my new business Brightwell Advisory and Ledger SA. Our services are accounting, tax, audit and financial management. Our customers are small companies, start-ups and new companies. The final design has to show financial security, trust and growth. Please find our logo attached to the business card. Text for the business card: Brightwell Advisory and Ledger SA Tomas Varenholt Director and Founder Certified Accountant Tel. 022 418 57 34 tv@clairevalconseil.ch www.clairevalconseil.ch Rue des Vergières 27 1201 Geneva
Target Market(s)
Our customers are small companies, start-ups and new companies.
Industry/Entity Type
Finance And Accounting
Contact Information for Business Card
Claireval Conseil et Comptes SA
Tomas Varenholt
Directeur et Fondateur
Expert-comptable diplômé
Tél. 022 418 57 34
tv@clairevalconseil.ch
www.clairevalconseil.ch
Rue des Vergières 27
1201 Genève

```html
<!DOCTYPE html>
<html lang="en">
<head>
<meta charset="utf-8">
<title>Claireval Conseil et Comptes SA — Business Card</title>
<link href="https://fonts.googleapis.com/css2?family=Lato:wght@400;700&display=swap" rel="stylesheet">
<style>
  :root {
    --backdrop: #2b2b2c;
    --card: #1c1d1f;
    --card-back: #18191b;
    --pattern-tone: #232427;
    --accent: #29abe2;
    --accent-deep: #1f7fc0;
    --text-main: #d2d3d5;
    --text-soft: #b4b6b9;
    --rule: #55585c;
  }
  * { margin: 0; padding: 0; box-sizing: border-box; }
  html, body {
    width: 1200px; height: 1108px; overflow: hidden;
    background: var(--backdrop);
  }
  .canvas {
    position: relative; width: 1200px; height: 1108px;
    display: flex; justify-content: center; align-items: center; gap: 60px;
    font-family: "Lato", sans-serif;
  }
  .card {
    width: 420px; height: 650px; border-radius: 26px;
    position: relative; overflow: hidden;
    box-shadow: 0 18px 40px rgba(0,0,0,.45);
  }
  .card-front {
    background: var(--card);
    display: flex; flex-direction: column; align-items: center;
    text-align: center; padding-top: 150px;
  }
  .brand-name {
    color: var(--text-main); font-weight: 400;
    font-size: 50px; letter-spacing: 4px; line-height: 1;
    text-transform: uppercase;
  }
  .brand-tagline {
    color: var(--text-main); font-weight: 400;
    font-size: 15px; letter-spacing: 4px; margin-top: 10px;
    text-transform: uppercase;
  }
  .holder-name {
    margin-top: 48px; color: var(--accent);
    font-size: 22px; font-weight: 400; text-transform: uppercase;
  }
  .holder-role {
    color: var(--text-soft); font-size: 19px; line-height: 1.3; margin-top: 4px;
  }
  .icon-divider {
    display: flex; align-items: center; gap: 6px; width: 260px; margin-top: 16px;
  }
  .icon-divider .rule { flex: 1; height: 1px; background: var(--rule); }
  .icon-divider svg { display: block; }
  .contact-list {
    list-style: none; color: var(--text-soft);
    font-size: 19px; line-height: 1.35; margin-top: 12px;
  }
  .plain-rule { width: 260px; height: 1px; background: var(--rule); margin-top: 14px; }
  .address { color: var(--text-soft); font-size: 19px; line-height: 1.35; margin-top: 12px; font-style: normal; }
  .card-back { background: var(--card-back); }
  .back-pattern {
    position: absolute; inset: 0;
    background: linear-gradient(160deg, var(--pattern-tone) 0%, var(--card-back) 75%);
  }
  .back-mark {
    position: absolute; left: 0; right: 0; bottom: 160px;
    text-align: center; color: var(--accent);
    font-size: 20px; font-weight: 400; letter-spacing: 3px; text-transform: uppercase;
  }
</style>
</head>
<body>
<main class="canvas">
  <section class="card card-front" aria-label="Card front">
    <div class="brand-name">Claireval</div>
    <div class="brand-tagline">Conseil et Comptes</div>

    <h1 class="holder-name">SA Tomas Varenholt</h1>
    <p class="holder-role">Director and Founder<br>Certified Accountant</p>

    <div class="icon-divider">
      <span class="rule"></span>
      <svg width="26" height="26" viewBox="0 0 26 26" aria-label="Phone">
        <circle cx="13" cy="13" r="12" fill="var(--accent)"/>
        <path d="M8 9c0-1 1-2 2-2l1.5 2.5-1 1.2c.7 1.6 2 2.9 3.6 3.6l1.2-1L18 15c0 1-1 2-2 2-4.5 0-8-3.5-8-8z" fill="var(--card)"/>
      </svg>
      <svg width="26" height="26" viewBox="0 0 26 26" aria-label="Email">
        <circle cx="13" cy="13" r="12" fill="var(--accent)"/>
        <rect x="7" y="9" width="12" height="8.5" fill="none" stroke="var(--card)" stroke-width="1.5"/>
        <path d="M7 9l6 5 6-5" fill="none" stroke="var(--card)" stroke-width="1.5"/>
      </svg>
      <svg width="26" height="26" viewBox="0 0 26 26" aria-label="Website">
        <circle cx="13" cy="13" r="12" fill="var(--accent)"/>
        <circle cx="13" cy="13" r="6" fill="none" stroke="var(--card)" stroke-width="1.5"/>
        <path d="M7 13h12M13 7c-2.5 3-2.5 9 0 12M13 7c2.5 3 2.5 9 0 12" fill="none" stroke="var(--card)" stroke-width="1.2"/>
      </svg>
      <span class="rule"></span>
    </div>

    <ul class="contact-list">
      <li>022 418 57 34</li>
      <li>tv@clairevalconseil.ch</li>
      <li>www.clairevalconseil.ch</li>
    </ul>
    <div class="plain-rule"></div>
    <address class="address">Rue des Vergières 27<br>1201 Geneva</address>
  </section>

  <section class="card card-back" aria-label="Card back">
    <div class="back-pattern" role="img" aria-label="Tone-on-tone repeating brand motif pattern"></div>
    <div class="back-mark">Claireval</div>
  </section>
</main>
</body>
</html>
```